The Linen Loft Co

We need a business card design for our wardrobe company.
Please visit our website www.gentlelinenlofts.com to get an idea of who we are.

```html
<!DOCTYPE html>
<html lang="en">
<head>
<meta charset="utf-8">
<title>The Linen Loft Co — Business Card</title>
<link href="https://fonts.googleapis.com/css2?family=Lato:wght@400;700&display=swap" rel="stylesheet">
<style>
  :root {
    --backdrop: #e7e3dd;
    --card-dark: #231f20;
    --card-light: #ffffff;
    --ink-light: #ffffff;
    --ink-dark: #1e1e1e;
    --ink-muted: #4a4a4a;
    --rule: #555555;
  }
  * { margin: 0; padding: 0; box-sizing: border-box; }
  html, body {
    width: 1200px; height: 960px; overflow: hidden;
    background: var(--backdrop);
    font-family: "Lato", Arial, sans-serif;
  }
  .canvas { position: relative; width: 1200px; height: 960px; }
  .card {
    position: absolute; left: 270px; width: 660px; height: 377px;
    box-shadow: 0 4px 10px rgba(0,0,0,0.25);
  }
  .card--front { top: 73px; background: var(--card-dark); color: var(--ink-light); }
  .card--back { top: 509px; background: var(--card-light); color: var(--ink-dark); }

  .front-square {
    position: absolute; left: 173px; top: 167px;
    width: 44px; height: 44px; border: 3px solid var(--ink-light);
  }
  .front-text { position: absolute; left: 279px; top: 161px; }
  .front-name {
    display: block;
    font-size: 19px; font-weight: 700; letter-spacing: 1.2px; text-transform: uppercase;
    line-height: 24px;
  }
  .front-tagline {
    display: block; margin-top: 9px; padding-left: 24px;
    font-size: 18px; font-weight: 700; line-height: 24px;
  }

  .back-brand {
    position: absolute; left: 90px; top: 136px; width: 210px; height: 106px;
    display: flex; align-items: center; justify-content: center; gap: 12px;
  }
  .back-square { width: 22px; height: 22px; border: 2px solid var(--ink-dark); flex: none; }
  .back-brand-name { font-size: 22px; font-weight: 700; color: var(--ink-dark); white-space: nowrap; }

  .divider {
    position: absolute; left: 329px; top: 110px; width: 2px; height: 157px;
    background: var(--rule);
  }
  .contact { position: absolute; left: 366px; top: 108px; }
  .contact-name { font-size: 20px; font-weight: 700; line-height: 22px; }
  .contact-role { font-size: 15.5px; color: var(--ink-muted); line-height: 20px; }
  .contact-address { margin-top: 15px; font-size: 15.5px; color: var(--ink-muted); line-height: 19px; }
  .contact-lines { margin-top: 10px; list-style: none; }
  .contact-lines li {
    display: flex; align-items: center; gap: 8px;
    font-size: 15.5px; color: var(--ink-muted); line-height: 19px;
  }
  .contact-lines svg { width: 12px; height: 12px; flex: none; }
</style>
</head>
<body>
<main class="canvas">
  <section class="card card--front" aria-label="Card front">
    <span class="front-square"></span>
    <div class="front-text">
      <span class="front-name">The Linen Loft Co</span>
      <span class="front-tagline">Made to Fit, Built to Last</span>
    </div>
  </section>

  <section class="card card--back" aria-label="Card back">
    <div class="back-brand">
      <span class="back-square"></span>
      <span class="back-brand-name">The Linen Loft Co</span>
    </div>
    <div class="divider"></div>
    <div class="contact">
      <p class="contact-name">Daniel Hartley</p>
      <p class="contact-role">Managing Director</p>
      <p class="contact-address">Harbour House, 42 Mill Lane<br>London E2 7QT</p>
      <ul class="contact-lines">
        <li>
          <svg viewBox="0 0 12 12" aria-hidden="true"><path d="M2.5 1 L4.5 1 L5 3.5 L3.8 4.4 Q4.8 6.6 7.3 8 L8.3 6.9 L11 7.5 L11 9.5 Q10.5 11 9 11 Q1 10 1 2.8 Q1 1 2.5 1 Z" fill="#4a4a4a"/></svg>
          0207 555 0148
        </li>
        <li>
          <svg viewBox="0 0 12 12" aria-hidden="true"><rect x="1" y="2.5" width="10" height="7" fill="none" stroke="#4a4a4a" stroke-width="1.2"/><path d="M1 2.5 L6 6.5 L11 2.5" fill="none" stroke="#4a4a4a" stroke-width="1.2"/></svg>
          info@gentlelinenlofts.com
        </li>
        <li>
          <svg viewBox="0 0 12 12" aria-hidden="true"><circle cx="6" cy="6" r="5" fill="none" stroke="#4a4a4a" stroke-width="1.1"/><ellipse cx="6" cy="6" rx="2.2" ry="5" fill="none" stroke="#4a4a4a" stroke-width="1"/><path d="M1 6 H11 M2 3.5 H10 M2 8.5 H10" stroke="#4a4a4a" stroke-width="0.9"/></svg>
          www.gentlelinenlofts.com
        </li>
      </ul>
    </div>
  </section>
</main>
</body>
</html>
```